Website Design for Landscaping/Concrete Company

I need a website that is informative about what my company does and also offers before and after pictures of completed work. I already have a logo. The website must say "FREE ESTIMATES" somewhere and list a phone number. I would like to stick with the logo colors or similar (black and lime green).
Services Offered by Tomlet Builders:
Landscaping
Mowing
Concrete
Sidewalks
Brush Removal
Land Beautification

Please list the company name in large letters TOMLET BUILDERS
and also the contact information in large font.

Right now I am looking for a somewhat coverpage for my website. I don't have a lot of information for people to point and click on yet. Id like to get a coverpage to get my name out and then have a designer come back in a few months and update with more pictures and information.
Updates

If allowed please submit projects after due date. I made a mistake and only posted for one day. Thanks.

Coding

Coded - Design and coding required

```html
<!DOCTYPE html>
<html lang="en">
<head>
<meta charset="utf-8">
<title>Tomlet Builders – Landscaping &amp; Concrete</title>
<link href="https://fonts.googleapis.com/css2?family=Montserrat:wght@500;600;700;800&family=Open+Sans:wght@400;600&display=swap" rel="stylesheet">
<style>
:root{
  --green:#7f9f05;
  --green-dark:#5f7a00;
  --ink:#1c1c1c;
  --text:#555;
  --soft:#f3f0ef;
  --white:#fff;
  --night:#111a0f;
}
*{box-sizing:border-box;margin:0;padding:0}
html,body{width:1200px;height:5063px;overflow:hidden}
body{font-family:"Open Sans",sans-serif;color:var(--text);background:var(--white);position:relative}
.abs{position:absolute}
h2.section-title{position:absolute;left:0;width:1200px;text-align:center;font-family:"Montserrat",sans-serif;font-weight:800;font-size:21px;color:var(--ink)}
h2.section-title::after{content:"";display:block;width:44px;height:2px;background:#999;margin:12px auto 0}
.btn{display:inline-block;background:var(--green);color:var(--white);font-family:"Montserrat",sans-serif;font-weight:700;text-align:center}

/* header */
.site-header{position:absolute;top:0;left:0;width:1200px;height:120px;background:var(--white)}
.brand{position:absolute;left:128px;top:36px;display:flex;align-items:center;gap:8px;font-family:"Montserrat",sans-serif;font-weight:800;font-size:17px;line-height:18px;color:var(--ink)}
.brand-mark{width:22px;height:22px;background:var(--green)}
.contact-chip{position:absolute;top:28px;display:flex;align-items:center;gap:10px}
.chip-icon{width:26px;height:26px;border-radius:50%;background:var(--green);display:flex;align-items:center;justify-content:center}
.chip-label{font-size:11px;color:var(--ink);line-height:13px}
.chip-value{font-size:17px;color:var(--ink);line-height:20px}
.header-cta{position:absolute;left:931px;top:27px;width:136px;height:33px;line-height:33px;font-size:13px}
.main-nav{position:absolute;top:84px;left:418px;display:flex;gap:0;font-family:"Montserrat",sans-serif;font-size:13px;font-weight:500;color:var(--ink)}
.main-nav a{color:inherit;text-decoration:none;margin-right:29px}
.main-nav a.active{color:var(--green);text-decoration:underline}

/* hero */
.hero{position:absolute;top:120px;left:0;width:1200px;height:605px;background:linear-gradient(160deg,#5d8a1e 0%,#7aab2b 35%,#4f7a1c 65%,#a59f8a 100%)}
.hero-title{position:absolute;top:188px;width:1200px;text-align:center;font-family:"Montserrat",sans-serif;font-weight:800;font-size:48px;color:var(--white);letter-spacing:1px}
.hero-sub{position:absolute;top:262px;width:1200px;text-align:center;font-family:"Montserrat",sans-serif;font-weight:700;font-size:19px;color:var(--white)}
.hero-cta{position:absolute;left:495px;top:318px;width:210px;height:48px;line-height:48px;background:var(--white);color:var(--green);font-size:21px;font-family:"Montserrat",sans-serif;font-weight:800;text-align:center}
.hero-dots{position:absolute;top:554px;left:565px;display:flex;gap:8px}
.hero-dots span{width:8px;height:8px;border-radius:50%;background:var(--white);opacity:.8}
.hero-dots span.on{background:transparent;border:1px solid #fff}

/* services */
.service-card{position:absolute;width:300px;height:392px;border:2px solid #2a2a2a;background:var(--white);text-align:center}
.service-photo{height:234px;width:100%}
.service-icon{position:absolute;left:120px;top:204px;width:58px;height:58px;border-radius:50%;background:var(--green);border:3px solid #fff;display:flex;align-items:center;justify-content:center}
.service-card h3{margin-top:46px;font-family:"Montserrat",sans-serif;font-weight:700;font-size:16px;color:var(--ink)}
.service-card p{margin:14px auto 0;width:240px;font-size:12.5px;line-height:20px;color:#333}
.service-card .btn{position:absolute;left:110px;bottom:-10px;width:78px;height:22px;line-height:22px;font-size:10px}

/* welcome */
.welcome{position:absolute;top:1756px;left:0;width:1200px;height:428px;background:var(--soft)}
.welcome-art{position:absolute;left:180px;top:0;width:280px;height:428px;background:linear-gradient(135deg,#6f9b2c,#9cc24b 50%,#c8c1b0)}
.welcome-kicker{position:absolute;left:612px;top:42px;font-family:"Montserrat",sans-serif;font-weight:700;font-size:16px;color:var(--ink)}
.welcome-title{position:absolute;left:612px;top:66px;font-family:"Montserrat",sans-serif;font-weight:800;font-size:29px;color:var(--ink)}
.welcome-rule{position:absolute;left:612px;top:120px;width:48px;height:2px;background:#999}
.welcome-text{position:absolute;left:612px;top:152px;width:440px;font-size:14px;line-height:22.5px;color:#666}
.welcome .btn{position:absolute;left:617px;top:344px;width:107px;height:30px;line-height:30px;font-size:13px}

/* why */
.why-hub{position:absolute;left:447px;top:2350px;width:310px;height:310px;border-radius:50%;background:radial-gradient(circle,#7cb02a,#4f8a17)}
.why-line{position:absolute;height:2px;background:var(--green)}
.why-icon{position:absolute;width:62px;height:62px;border-radius:50%;background:var(--green);display:flex;align-items:center;justify-content:center}
.why-item{position:absolute;width:215px}
.why-item h4{font-family:"Montserrat",sans-serif;font-weight:700;font-size:13.5px;color:var(--ink);margin-bottom:4px}
.why-item p{font-size:11.5px;line-height:16px;color:#555}

/* testimonials */
.testimonials{position:absolute;top:2740px;left:0;width:1200px;height:432px;background:linear-gradient(180deg,#e3e3e1,#cfcfcb)}
.quote-card{position:absolute;top:145px;width:300px;height:198px;background:var(--white);border:1px solid #ddd;text-align:center}
.quote-mark{position:absolute;top:-18px;left:130px;width:40px;font-family:"Montserrat",sans-serif;font-weight:800;font-size:40px;line-height:40px;color:var(--green)}
.quote-card p{margin:38px auto 0;width:250px;font-size:12px;line-height:18px;color:#333}
.avatar{position:absolute;top:323px;width:44px;height:44px;border-radius:50%;background:#8d7a6a;border:2px solid #fff}
.quote-name{position:absolute;top:376px;width:300px;text-align:center;font-size:10px;color:#333}
.arrow{position:absolute;top:235px}

/* gallery */
.gallery-tile{position:absolute;width:228px;height:192px}
.gallery .btn{position:absolute;left:524px;top:3728px;width:144px;height:32px;line-height:32px;font-size:14px}

/* blog */
.blog{position:absolute;top:3800px;left:0;width:1200px;height:545px;background:var(--soft)}
.blog-card{position:absolute;top:117px;width:300px;height:378px;background:var(--white);box-shadow:0 2px 8px rgba(0,0,0,.08)}
.blog-photo{height:182px}
.blog-card h3{margin:30px 0 0 28px;width:250px;font-family:"Montserrat",sans-serif;font-weight:600;font-size:12px;line-height:20px;color:var(--ink)}
.blog-card p{margin:14px 0 0 28px;width:240px;font-size:11px;line-height:16px;color:#555}
.blog-card .btn{position:absolute;left:28px;top:328px;width:84px;height:22px;line-height:22px;font-size:10px;font-weight:600}

/* contact */
.contact{position:absolute;top:4345px;left:0;width:1200px;height:505px;background:linear-gradient(160deg,#1e2a17,#0f150c 60%,#1b2414)}
.contact h2.section-title{color:var(--white)}
.contact h2.section-title::after{background:#aaa}
.contact-row{position:absolute;left:205px;display:flex;align-items:center;gap:22px;color:var(--white);font-size:13.5px;line-height:20px}
.ring{width:44px;height:44px;border-radius:50%;border:2px solid #fff;display:flex;align-items:center;justify-content:center}
.follow{position:absolute;left:207px;top:405px;display:flex;align-items:center;gap:8px;color:var(--white);font-size:13px}
.social{width:24px;height:24px;border-radius:50%}
.field{position:absolute;left:641px;width:335px;height:42px;background:var(--white);font-size:11.5px;color:#333;padding:14px 14px}
.submit{position:absolute;left:641px;top:412px;width:335px;height:41px;line-height:41px;font-size:18px}

/* footer */
.site-footer{position:absolute;top:4850px;left:0;width:1200px;height:213px;background:#000;text-align:center}
.footer-brand{position:absolute;top:80px;width:1200px;font-family:"Montserrat",sans-serif;font-weight:800;font-size:22px;color:var(--green)}
.copyright{position:absolute;top:172px;width:1200px;font-size:10.5px;color:#bbb}
</style>
</head>
<body>

<header class="site-header">
  <div class="brand"><span class="brand-mark"></span><span>TOMLET<br>BUILDERS</span></div>
  <div class="contact-chip" style="left:546px">
    <span class="chip-icon"><svg width="14" height="10" viewBox="0 0 14 10"><rect x="0.5" y="0.5" width="13" height="9" fill="#fff"/><path d="M1 1l6 5 6-5" stroke="#7f9f05" fill="none"/></svg></span>
    <div><div class="chip-label">E MAIL US</div><div class="chip-value">info@tomlet.com</div></div>
  </div>
  <div class="contact-chip" style="left:746px">
    <span class="chip-icon"><svg width="14" height="14" viewBox="0 0 24 24"><path fill="#fff" d="M6.6 10.8a15 15 0 006.6 6.6l2.2-2.2c.3-.3.7-.4 1-.2 1.1.4 2.3.6 3.6.6.6 0 1 .4 1 1V20c0 .6-.4 1-1 1A17 17 0 013 4c0-.6.4-1 1-1h3.5c.6 0 1 .4 1 1 0 1.3.2 2.5.6 3.6.1.3 0 .7-.2 1z"/></svg></span>
    <div><div class="chip-label">CALL US</div><div class="chip-value">555.014.2280</div></div>
  </div>
  <span class="btn header-cta">FREE ESTIMATES</span>
  <nav class="main-nav">
    <a class="active">HOME</a><a>ABOUT US</a><a>SERVICES</a><a>TESTIMONIALS</a><a>GALLERY</a><a>BLOG</a><a style="margin-right:0">CONTACT</a>
  </nav>
</header>

<section class="hero" role="img" aria-label="Landscaped lawn with a curving brick paver path">
  <h1 class="hero-title">LANDSCAPING</h1>
  <p class="hero-sub">LOREM IPSUM IS SIMPLY DUMMY TEXT OF THE PRINTING</p>
  <span class="hero-cta">FREE ESTIMATES</span>
  <div class="hero-dots"><span></span><span></span><span class="on"></span><span></span><span></span></div>
</section>

<section class="services">
  <h2 class="section-title" style="top:760px">OUR SERVICES</h2>

  <article class="service-card" style="left:128px;top:842px">
    <div class="service-photo" role="img" aria-label="Garden path lined with hedges and flowers" style="background:linear-gradient(160deg,#6a9a2c,#a6b58c 50%,#b8405a)"></div>
    <span class="service-icon"><svg width="26" height="26" viewBox="0 0 24 24"><path fill="#fff" d="M12 3c4 3 6 6 6 9a6 6 0 01-12 0c0-3 2-6 6-9z"/></svg></span>
    <h3>Landscaping</h3>
    <p>Lorem Ipsum is simply dummy text of the printing and typesetting .</p>
    <span class="btn">Read more</span>
  </article>
  <article class="service-card" style="left:450px;top:842px">
    <div class="service-photo" role="img" aria-label="Lawn mower cutting grass" style="background:linear-gradient(160deg,#3f6e1c,#7ab52e 60%,#4a7e1a)"></div>
    <span class="service-icon"><svg width="26" height="26" viewBox="0 0 24 24"><path fill="#fff" d="M4 13h13v4H4z"/><circle cx="7" cy="18.5" r="2.5" fill="#fff"/><circle cx="15" cy="18.5" r="2.5" fill="#fff"/><path d="M16 13l4-8" stroke="#fff" stroke-width="2"/></svg></span>
    <h3>Mowing</h3>
    <p>Lorem Ipsum is simply dummy text of the printing and typesetting .</p>
    <span class="btn">Read more</span>
  </article>
  <article class="service-card" style="left:771px;top:842px">
    <div class="service-photo" role="img" aria-label="Workers pouring concrete" style="background:linear-gradient(160deg,#c9924c,#8b8780 50%,#6d6a66)"></div>
    <span class="service-icon"><svg width="26" height="26" viewBox="0 0 24 24"><path fill="#fff" d="M3 8h11v8H3zM14 11h4l3 3v2h-7z"/><circle cx="7" cy="18" r="2" fill="#fff"/><circle cx="17" cy="18" r="2" fill="#fff"/></svg></span>
    <h3>Concrete</h3>
    <p>Lorem Ipsum is simply dummy text of the printing and typesetting .</p>
    <span class="btn">Read more</span>
  </article>

  <article class="service-card" style="left:128px;top:1276px">
    <div class="service-photo" role="img" aria-label="Curved brick sidewalk through a lawn" style="background:linear-gradient(160deg,#5a8d24,#b49a8a 50%,#6e9a30)"></div>
    <span class="service-icon"><svg width="26" height="26" viewBox="0 0 24 24"><path d="M12 3v18M6 7h12M6 7l-3 6h6zM18 7l-3 6h6z" stroke="#fff" stroke-width="1.6" fill="none"/></svg></span>
    <h3>Sidewalks</h3>
    <p>Lorem Ipsum is simply dummy text of the printing and typesetting .</p>
    <span class="btn">Read more</span>
  </article>
  <article class="service-card" style="left:450px;top:1276px">
    <div class="service-photo" role="img" aria-label="Rake gathering autumn leaves" style="background:linear-gradient(160deg,#d9a25a,#a65a2a 50%,#6a4024)"></div>
    <span class="service-icon"><svg width="26" height="26" viewBox="0 0 24 24"><path d="M19 3L9 13" stroke="#fff" stroke-width="2.4"/><path fill="#fff" d="M9 11l4 4-6 6-4-4z"/></svg></span>
    <h3>Brush Removal</h3>
    <p>Lorem Ipsum is simply dummy text of the printing and typesetting .</p>
    <span class="btn">Read more</span>
  </article>
  <article class="service-card" style="left:771px;top:1276px">
    <div class="service-photo" role="img" aria-label="Neatly trimmed hedge rows" style="background:linear-gradient(160deg,#2f5e16,#5f9a22 50%,#3e7518)"></div>
    <span class="service-icon"><svg width="26" height="26" viewBox="0 0 24 24"><circle cx="12" cy="9" r="6" stroke="#fff" stroke-width="1.6" fill="none"/><path d="M12 15v6M8 21h8" stroke="#fff" stroke-width="1.6"/></svg></span>
    <h3>Land Beautification</h3>
    <p>Lorem Ipsum is simply dummy text of the printing and typesetting .</p>
    <span class="btn">Read more</span>
  </article>
</section>

<section class="welcome">
  <div class="welcome-art" role="img" aria-label="Lawn and paver path photograph"></div>
  <div class="welcome-kicker">WELCOME TO</div>
  <div class="welcome-title">TOMLET BUILDERS</div>
  <div class="welcome-rule"></div>
  <p class="welcome-text">Lorem ipsum dolor sit amet, consectetur adipiscing elit, sed do eiusmod tempor incididunt ut labore et dolore magna aliqua. Ut enim ad minim veniam, quis nostrud exercitation ullamco laboris nisi ut aliquip ex ea commodo consequat. Duis aute irure dolor in reprehenderit in voluptate velit esse cillum dolore eu fugiat nulla pariatur. Excepteur sint occaecat cupidatat non proident, sunt in culpa qui officia deserunt mollit anim id est laborum</p>
  <span class="btn">Read more</span>
</section>

<section class="why">
  <h2 class="section-title" style="top:2241px">WHY CHOOSE US</h2>
  <div class="why-line" style="left:448px;top:2385px;width:60px"></div>
  <div class="why-line" style="left:448px;top:2500px;width:40px"></div>
  <div class="why-line" style="left:448px;top:2615px;width:60px"></div>
  <div class="why-line" style="left:696px;top:2385px;width:60px"></div>
  <div class="why-line" style="left:716px;top:2500px;width:40px"></div>
  <div class="why-line" style="left:696px;top:2615px;width:60px"></div>
  <div class="why-hub" role="img" aria-label="Lawn mower on fresh cut grass"></div>

  <span class="why-icon" style="left:386px;top:2354px"><svg width="30" height="30" viewBox="0 0 24 24"><circle cx="8" cy="8" r="2.5" fill="#fff"/><circle cx="16" cy="8" r="2.5" fill="#fff"/><path fill="#fff" d="M4 20v-6a4 4 0 018 0v6zM12 20v-6a4 4 0 018 0v6z"/></svg></span>
  <span class="why-icon" style="left:369px;top:2469px"><svg width="30" height="30" viewBox="0 0 24 24"><path fill="#fff" d="M3 10h4v10H3zM9 20V10l4-7c1.5 0 2 1 2 2l-1 4h6c1 0 2 1 1.7 2.2l-1.8 7A2 2 0 0118 20z"/></svg></span>
  <span class="why-icon" style="left:386px;top:2584px"><svg width="30" height="30" viewBox="0 0 24 24"><path fill="#fff" d="M6.6 10.8a15 15 0 006.6 6.6l2.2-2.2c.3-.3.7-.4 1-.2 1.1.4 2.3.6 3.6.6.6 0 1 .4 1 1V20c0 .6-.4 1-1 1A17 17 0 013 4c0-.6.4-1 1-1h3.5c.6 0 1 .4 1 1 0 1.3.2 2.5.6 3.6.1.3 0 .7-.2 1z"/></svg></span>
  <span class="why-icon" style="left:772px;top:2354px"><svg width="30" height="30" viewBox="0 0 24 24"><path fill="#fff" d="M12 6l9 15H3z"/><path d="M12 6V2l5 2-5 2" stroke="#fff" fill="#fff"/></svg></span>
  <span class="why-icon" style="left:789px;top:2469px"><svg width="30" height="30" viewBox="0 0 24 24"><circle cx="12" cy="12" r="7" stroke="#fff" stroke-width="4" fill="none" stroke-dasharray="3 2.5"/><circle cx="12" cy="12" r="3" fill="#fff"/></svg></span>
  <span class="why-icon" style="left:772px;top:2584px"><svg width="30" height="30" viewBox="0 0 24 24"><circle cx="12" cy="8" r="4" fill="#fff"/><path fill="#fff" d="M4 21a8 8 0 0116 0z"/></svg></span>

  <div class="why-item" style="left:131px;top:2349px"><h4>Team Expert</h4><p>Lorem ipsum dolor sit amet, consec tetur adipiscing elit, sed do eiusmod tempor incididunt lorem.</p></div>
  <div class="why-item" style="left:131px;top:2463px"><h4>Customer Satisfaction</h4><p>Lorem ipsum dolor sit amet, consec tetur adipiscing elit, sed do eiusmod tempor incididunt lorem.</p></div>
  <div class="why-item" style="left:131px;top:2577px"><h4>Support</h4><p>Lorem ipsum dolor sit amet, consec tetur adipiscing elit, sed do eiusmod tempor incididunt lorem.</p></div>
  <div class="why-item" style="left:871px;top:2349px"><h4>Mission &amp; Vision</h4><p>Lorem ipsum dolor sit amet, consec tetur adipiscing elit, sed do eiusmod tempor incididunt lorem.</p></div>
  <div class="why-item" style="left:871px;top:2463px"><h4>Best Service</h4><p>Lorem ipsum dolor sit amet, consec tetur adipiscing elit, sed do eiusmod tempor incididunt lorem.</p></div>
  <div class="why-item" style="left:871px;top:2577px"><h4>Professional</h4><p>Lorem ipsum dolor sit amet, consec tetur adipiscing elit, sed do eiusmod tempor incididunt lorem.</p></div>
</section>

<section class="testimonials" aria-label="Testimonials">
  <h2 class="section-title" style="top:38px">TESTIMONIALS</h2>
  <svg class="arrow" style="left:66px" width="14" height="20" viewBox="0 0 14 20"><path d="M11 2L3 10l8 8" stroke="#7f9f05" stroke-width="2.5" fill="none"/></svg>
  <svg class="arrow" style="left:1116px" width="14" height="20" viewBox="0 0 14 20"><path d="M3 2l8 8-8 8" stroke="#7f9f05" stroke-width="2.5" fill="none"/></svg>

  <div class="quote-card" style="left:130px"><span class="quote-mark">“</span><p>On the other hand, we denounce with righteous indignation and dislike men who are so beguiled and demoralized by the charms of pleasure of the moment, so blinded by desire, that they cannot foresee the pain and trouble that are bound to ensue; and equal blame .</p></div>
  <div class="quote-card" style="left:451px"><span class="quote-mark">“</span><p>On the other hand, we denounce with righteous indignation and dislike men who are so beguiled and demoralized by the charms of pleasure of the moment, so blinded by desire, that they cannot foresee the pain and trouble that are bound to ensue; and equal blame .</p></div>
  <div class="quote-card" style="left:768px"><span class="quote-mark">“</span><p>On the other hand, we denounce with righteous indignation and dislike men who are so beguiled and demoralized by the charms of pleasure of the moment, so blinded by desire, that they cannot foresee the pain and trouble that are bound to ensue; and equal blame .</p></div>

  <span class="avatar" style="left:258px" role="img" aria-label="Client portrait"></span>
  <span class="avatar" style="left:579px;background:#8a3a34" role="img" aria-label="Client portrait"></span>
  <span class="avatar" style="left:896px;background:#5a6b7a" role="img" aria-label="Client portrait"></span>
  <span class="quote-name" style="left:130px">DANIEL, England</span>
  <span class="quote-name" style="left:451px">DANIEL, England</span>
  <span class="quote-name" style="left:768px">DANIEL, England</span>
</section>

<section class="gallery">
  <h2 class="section-title" style="top:3218px">GALLERY</h2>
  <div class="gallery-tile" style="left:130px;top:3292px;background:linear-gradient(160deg,#a8a040,#6b8a24)" role="img" aria-label="Gardener trimming lawn edges"></div>
  <div class="gallery-tile" style="left:367px;top:3292px;background:linear-gradient(160deg,#4a8a1e,#2f6a12)" role="img" aria-label="Mower on lawn from above"></div>
  <div class="gallery-tile" style="left:603px;top:3292px;background:linear-gradient(160deg,#5a9a2a,#c86a50 70%,#4f8a22)" role="img" aria-label="Flower beds and lawn"></div>
  <div class="gallery-tile" style="left:839px;top:3292px;background:linear-gradient(160deg,#c8b860,#6a9a30 50%,#9aa890)" role="img" aria-label="Stepping stone path in garden"></div>
  <div class="gallery-tile" style="left:130px;top:3491px;background:linear-gradient(160deg,#4a7a2a,#c04858 50%,#a89a8a)" role="img" aria-label="Garden steps with flowers"></div>
  <div class="gallery-tile" style="left:367px;top:3491px;background:linear-gradient(160deg,#4a7a28,#b0a8a0 50%,#5a9a2a)" role="img" aria-label="Curving paver walkway"></div>
  <div class="gallery-tile" style="left:603px;top:3491px;background:linear-gradient(160deg,#6a9a3a,#8a6a50 50%,#b0a8a0)" role="img" aria-label="Stone steps with plantings"></div>
  <div class="gallery-tile" style="left:839px;top:3491px;background:linear-gradient(160deg,#2a4a18,#5a8a2a 50%,#2e5218)" role="img" aria-label="Hedge archway"></div>
  <span class="btn">View all images</span>
</section>

<section class="blog">
  <h2 class="section-title" style="top:41px">LATEST BLOG</h2>
  <article class="blog-card" style="left:126px">
    <div class="blog-photo" role="img" aria-label="Lawn beside a garden wall" style="background:linear-gradient(160deg,#a89a60,#5e9a26 50%,#3e7a18)"></div>
    <h3>LOREM IPSUM IS SIMPLY DUMMY TEXT OF THE PRINTING</h3>
    <p>Lorem Ipsum is simply dummy text of the printing and typesetting industry standard dummy text ever.</p>
    <span class="btn">READ MORE</span>
  </article>
  <article class="blog-card" style="left:451px">
    <div class="blog-photo" role="img" aria-label="Garden archway over path" style="background:linear-gradient(160deg,#4a7a20,#9ac040 50%,#3a6a18)"></div>
    <h3>LOREM IPSUM IS SIMPLY DUMMY TEXT OF THE PRINTING</h3>
    <p>Lorem Ipsum is simply dummy text of the printing and typesetting industry standard dummy text ever.</p>
    <span class="btn">READ MORE</span>
  </article>
  <article class="blog-card" style="left:775px">
    <div class="blog-photo" role="img" aria-label="Lawn with shrubs and house" style="background:linear-gradient(160deg,#c8c8c0,#5a9a2a 50%,#3e7a18)"></div>
    <h3>LOREM IPSUM IS SIMPLY DUMMY TEXT OF THE PRINTING</h3>
    <p>Lorem Ipsum is simply dummy text of the printing and typesetting industry standard dummy text ever.</p>
    <span class="btn">READ MORE</span>
  </article>
</section>

<section class="contact" role="region" aria-label="Contact us, over a darkened garden photograph">
  <h2 class="section-title" style="top:42px">CONTACT US</h2>
  <div class="contact-row" style="top:140px">
    <span class="ring"><svg width="16" height="18" viewBox="0 0 24 24"><path fill="#fff" d="M12 2a7 7 0 00-7 7c0 5 7 13 7 13s7-8 7-13a7 7 0 00-7-7zm0 9.5A2.5 2.5 0 1112 6a2.5 2.5 0 010 5.5z"/></svg></span>
    <div>2250 MAPLE RIDGE ROAD<br>FAIRVIEW, CA 90310</div>
  </div>
  <div class="contact-row" style="top:213px">
    <span class="ring"><svg width="16" height="16" viewBox="0 0 24 24"><path fill="#fff" d="M6.6 10.8a15 15 0 006.6 6.6l2.2-2.2c.3-.3.7-.4 1-.2 1.1.4 2.3.6 3.6.6.6 0 1 .4 1 1V20c0 .6-.4 1-1 1A17 17 0 013 4c0-.6.4-1 1-1h3.5c.6 0 1 .4 1 1 0 1.3.2 2.5.6 3.6.1.3 0 .7-.2 1z"/></svg></span>
    <div>CALL US<br>555.014.2280</div>
  </div>
  <div class="contact-row" style="top:287px">
    <span class="ring"><svg width="16" height="12" viewBox="0 0 14 10"><rect x="0.5" y="0.5" width="13" height="9" fill="#fff"/><path d="M1 1l6 5 6-5" stroke="#111" fill="none"/></svg></span>
    <div>E MAIL US<br>info@tomletbuilders.com</div>
  </div>
  <div class="follow">FOLLOW US
    <span class="social" style="margin-left:22px;background:#3b5ab0"></span>
    <span class="social" style="background:#2aa3e8"></span>
    <span class="social" style="background:#1a6fb0"></span>
  </div>

  <div class="field" style="top:145px">NAME</div>
  <div class="field" style="top:194px">E MAIL ID</div>
  <div class="field" style="top:244px">PHONE</div>
  <div class="field" style="top:294px;height:102px">MESSAGE</div>
  <span class="btn submit">SUBMIT</span>
</section>

<footer class="site-footer">
  <div class="footer-brand">TOMLET BUILDERS</div>
  <div class="copyright">Copyright © 2020 All Rights Reserved</div>
</footer>

</body>
</html>
```